Set up small scale company website

We need a website set up for our educational consultancy - Vexmore Education. We like the following site and want something similar www.plindarhub.co.uk We can provide the copy and images but need the following:- setting up the overall theme and design - to our requirements on colours and forma- Approximately 4 pages of services offered and with an index pageEtct (yellow and green)And the following pages - as well as a home page:- A contact page linked to our email addresses and registered business address 17 Wexbury Lane, Harwich, Essex, CO14 8PN- About Us page - An index of services page that links to between 4-6 pages outlining services- A News page that links to updates of latest services, events and activities - easily updated by usOn the homepage we'd like links to chirpnet and WorkLoop feeds and links to our other blogs and websites
Target Market(s)
Schools, local authoroties and multi-academy trusts
Logo Text
Vexmore Education
Coding
Coded - Design and coding required
Number of Pages Required
5+ page
Font styles to use
Requirements
Should not have
- No tacky pictures of mortar boards or chalk boards etc.

```html
<!DOCTYPE html>
<html lang="en">
<head>
<meta charset="utf-8">
<title>Vexmore Education – Home</title>
<link rel="stylesheet" href="https://fonts.googleapis.com/css2?family=Montserrat:wght@600;700&family=Open+Sans:wght@400;600;700&display=swap">
<style>
:root{
  --canvas:#e4e4e4;
  --white:#ffffff;
  --panel:#f1f1f1;
  --ink:#2b2b2b;
  --text:#555555;
  --muted:#8a8a8a;
  --yellow:#f7ec5c;
  --button:#f2e600;
  --green:#b9d960;
  --green-deep:#8cc63f;
  --link:#29a8e0;
  --card-edge:#efe6a0;
}
*{box-sizing:border-box;margin:0;padding:0}
html,body{width:1200px;height:1096px;overflow:hidden;background:var(--canvas)}
body{font-family:"Open Sans",Arial,sans-serif;color:var(--text)}
.page{position:absolute;left:350px;top:0;width:500px;height:1096px;background:var(--white);overflow:hidden}
.abs{position:absolute}
.brand{display:flex;align-items:center;gap:6px;font-family:"Montserrat",Arial,sans-serif;font-weight:700;color:var(--ink)}
.brand-dot{border-radius:50%;background:var(--green-deep);flex:none}
.heading{font-family:"Montserrat",Arial,sans-serif;font-weight:700;color:var(--ink);text-transform:uppercase}
.btn{display:inline-block;background:var(--button);color:var(--ink);font-family:"Montserrat",Arial,sans-serif;font-weight:700;font-size:6.5px;padding:5px 8px;border-bottom:2px solid #d9c900;text-transform:uppercase}

/* header */
.site-header{left:0;top:0;width:500px;height:47px}
.site-header .brand{position:absolute;left:10px;top:12px;font-size:10.5px}
.contact-strip{position:absolute;right:16px;top:6px;display:flex;gap:18px;font-size:6px;font-weight:600;color:var(--ink)}
.contact-strip span{display:flex;align-items:center;gap:3px}
.main-nav{position:absolute;right:20px;top:28px;display:flex;gap:14px;font-family:"Montserrat",Arial,sans-serif;font-size:5.8px;font-weight:700;color:var(--ink)}
.main-nav a{position:relative;color:inherit;text-decoration:none}
.main-nav a.active::after{content:"";position:absolute;left:0;right:0;bottom:-11px;height:2px;background:var(--green-deep)}

/* hero */
.hero{left:0;top:47px;width:500px;height:212px}
.hero-photo{position:absolute;left:0;top:0;width:330px;height:212px;background:linear-gradient(135deg,#7a6a52 0%,#4d5566 45%,#a48a6a 100%)}
.hero-curve{position:absolute;left:0;top:0}
.hero-copy{position:absolute;left:326px;top:46px;width:150px}
.hero-copy h1{font-size:14px;margin-bottom:8px}
.hero-copy p{font-size:6px;line-height:1.55;margin-bottom:10px}
.dots{display:flex;gap:4px}
.dots i{width:3px;height:3px;border-radius:50%;background:var(--ink);display:block}
.dots i.off{background:#bbb}

/* welcome */
.welcome{left:0;top:259px;width:500px;height:271px;background:var(--panel)}
.welcome h2{position:absolute;left:25px;top:22px;font-size:12.5px}
.welcome-photo{position:absolute;left:25px;top:42px;width:255px;height:118px;background:linear-gradient(120deg,#5f7ea3 0%,#c6b9a8 55%,#3b3f4c 100%)}
.welcome p{position:absolute;left:25px;top:169px;width:262px;font-size:6.4px;line-height:1.75}
.welcome .btn{position:absolute;left:25px;top:219px}
.services{position:absolute;left:305px;top:14px;width:174px}
.services h3{background:var(--white);font-size:11.5px;padding:11px 20px 10px}
.services ul{list-style:none}
.services li{height:28px;display:flex;align-items:center;padding-left:22px;font-size:6.4px;font-weight:700;color:var(--ink)}
.services li::before{content:"›";margin-right:10px;font-size:9px}
.services li:nth-child(odd){background:var(--green)}
.services li:nth-child(even){background:var(--yellow)}

/* social */
.social{left:0;top:530px;width:500px;height:253px;background:var(--white)}
.tabs{position:absolute;left:0;width:500px;top:16px;display:flex;justify-content:center;gap:22px;font-family:"Montserrat",Arial,sans-serif;font-weight:700;font-size:10.5px;color:var(--ink)}
.tab{display:flex;align-items:center;gap:5px;padding:0 8px 5px;position:relative}
.tab .mark{width:7px;height:7px;border-radius:50%;background:var(--ink)}
.tab.active{border-bottom:2px solid var(--link)}
.tab.active::after{content:"";position:absolute;left:50%;bottom:-6px;margin-left:-4px;border:4px solid transparent;border-top-color:var(--link);border-bottom:0}
.feed{position:absolute;left:31px;top:64px;display:flex;gap:9px}
.post{width:102px;height:133px;background:var(--panel);border:1px solid var(--card-edge);padding:9px 7px}
.post.raised{background:var(--white);border-color:transparent;box-shadow:0 3px 8px rgba(0,0,0,.14)}
.post p{font-size:5.6px;line-height:1.8;color:var(--ink)}
.post p em{font-style:normal;color:var(--link)}
.post .brand{margin-top:14px;font-size:6.4px;gap:5px}
.post .brand-dot{width:11px;height:11px}
.post time{display:block;margin-left:23px;font-size:5.5px;font-weight:700;color:var(--green-deep)}
.social .dots{position:absolute;left:237px;top:226px}

/* blog */
.blog{left:0;top:783px;width:500px;height:204px;background:#ececec}
.blog h2{position:absolute;left:0;width:500px;top:22px;text-align:center;font-size:11px}
.posts{position:absolute;left:7px;top:48px;display:flex;gap:13px}
.article{width:157px;position:relative;height:156px}
.article-photo{position:absolute;left:0;top:0;width:157px;height:98px}
.article-body{position:absolute;left:7px;top:82px;width:143px;height:74px;background:var(--white);text-align:center;padding-top:9px}
.article-body h3{font-size:8px;margin-bottom:5px}
.article-body p{font-size:5.6px;line-height:1.7;color:var(--ink)}
.plus{position:absolute;left:50%;bottom:0;transform:translateX(-50%);width:14px;height:14px;font-size:9px;line-height:14px;color:var(--ink);font-weight:700}
.plus::after{content:"";position:absolute;left:0;right:0;bottom:-2px;height:2px;background:var(--green-deep)}
.plus.filled{background:var(--green-deep);color:var(--white);bottom:6px}
.plus.filled::after{display:none}

/* footer */
.site-footer{left:0;top:987px;width:500px;height:109px;background:#f4f4f4}
.site-footer .brand{position:absolute;left:18px;top:26px;font-size:10.5px}
.site-footer .brand-dot{width:18px;height:18px}
.legal{position:absolute;left:57px;top:44px;font-size:5.8px;color:var(--ink)}
.footer-icons{position:absolute;left:57px;top:58px;display:flex;gap:11px}
.footer-icons i{width:5px;height:5px;border-radius:50%;background:var(--ink);display:block}
.footer-nav{position:absolute;left:185px;top:33px;display:flex;gap:13px;font-family:"Montserrat",Arial,sans-serif;font-weight:700;font-size:5.8px;color:var(--ink)}
.address{position:absolute;left:395px;top:29px;width:90px;font-size:5.8px;line-height:1.75;color:var(--ink);display:flex;gap:5px}
</style>
</head>
<body>
<div class="page">

  <header class="site-header abs">
    <div class="brand"><span class="brand-dot" style="width:20px;height:20px"></span>VEXMORE EDUCATION</div>
    <div class="contact-strip">
      <span><svg width="6" height="6" viewBox="0 0 10 10"><path d="M2 0h2l1 3-1.5 1a6 6 0 0 0 2.5 2.5L7 5l3 1v2c0 1-1 2-2 2A8 8 0 0 1 0 2c0-1 1-2 2-2z" fill="#2b2b2b"/></svg>1-800 555 0142</span>
      <span><svg width="6" height="5" viewBox="0 0 10 8"><rect width="10" height="8" fill="#2b2b2b"/><path d="M0 0l5 4 5-4" stroke="#fff" fill="none"/></svg>hello@vexmoremail.com</span>
    </div>
    <nav class="main-nav">
      <a class="active">HOME</a><a>SERVICES</a><a>NEWS</a><a>ABOUT US</a><a>CONTACT US</a>
    </nav>
  </header>

  <section class="hero abs">
    <div class="hero-photo" role="img" aria-label="Teacher helping two pupils at a library table"></div>
    <svg class="hero-curve" width="500" height="212" viewBox="0 0 500 212">
      <path d="M330 0 Q280 100 318 212 L500 212 L500 0 Z" fill="#fff"/>
      <path d="M330 0 Q280 100 318 212 L326 212 Q291 105 338 0 Z" fill="#8cc63f"/>
    </svg>
    <div class="hero-copy">
      <h1 class="heading">Vexmore Education</h1>
      <p>Sed ut perspiciatis unde omnis iste natus error sit voluptatem accusantium doloremque laudantium, totam rem aperiam, eaque ipsa quae ab illo inventore veritatis...</p>
      <a class="btn">Learn More</a>
      <div class="dots" style="margin-top:24px;margin-left:6px"><i></i><i class="off"></i><i></i></div>
    </div>
  </section>

  <section class="welcome abs">
    <h2 class="heading">Welcome to Vexmore Education</h2>
    <div class="welcome-photo" role="img" aria-label="Pupil working at a computer in a classroom"></div>
    <p>Sed ut perspiciatis unde omnis iste natus error sit voluptatem accusantium doloremque laudantium, totam rem aperiam, eaque ipsa quae ab illo inventore veritatis et quasi architecto beatae vitae dicta sunt explicabo.</p>
    <a class="btn">Learn More</a>
    <div class="services">
      <h3 class="heading">Our Services</h3>
      <ul>
        <li>Finibus Bonorum</li>
        <li>Nam libero tempore</li>
        <li>Et harum quidem rerum</li>
        <li>Laborious physical exercise</li>
        <li>Finibus Bonorum</li>
        <li>Nam libero tempore</li>
        <li>Et harum quidem rerum</li>
      </ul>
    </div>
  </section>

  <section class="social abs">
    <div class="tabs">
      <div class="tab active"><span class="mark"></span>chirpnet</div>
      <div class="tab"><span class="mark"></span>WorkLoop</div>
    </div>
    <div class="feed">
      <article class="post">
        <p>On the other hand, we denounce with righteous indignation and dislike men <em>@Brightpath</em> and demoralized by the charms of pleasure of the moment, so blinded by desire.<em>http://qlu.com</em></p>
        <div class="brand"><span class="brand-dot"></span>VEXMORE EDUCATION</div>
        <time>Feb 2 - 2019</time>
      </article>
      <article class="post raised">
        <p>On the other hand, we denounce with righteous indignation and dislike men <em>@Brightpath</em> and demoralized by the charms of pleasure of the moment, so blinded by desire.<em>http://qlu.com</em></p>
        <div class="brand"><span class="brand-dot"></span>VEXMORE EDUCATION</div>
        <time>Feb 2 - 2019</time>
      </article>
      <article class="post">
        <p>On the other hand, we denounce with righteous indignation and dislike men <em>@Brightpath</em> and demoralized by the charms of pleasure of the moment, so blinded by desire.<em>http://qlu.com</em></p>
        <div class="brand"><span class="brand-dot"></span>VEXMORE EDUCATION</div>
        <time>Feb 2 - 2019</time>
      </article>
      <article class="post">
        <p>On the other hand, we denounce with righteous indignation and dislike men <em>@Brightpath</em> and demoralized by the charms of pleasure of the moment, so blinded by desire.<em>http://qlu.com</em></p>
        <div class="brand"><span class="brand-dot"></span>VEXMORE EDUCATION</div>
        <time>Feb 2 - 2019</time>
      </article>
    </div>
    <div class="dots"><i></i><i class="off"></i><i></i></div>
  </section>

  <section class="blog abs">
    <h2 class="heading">Blog</h2>
    <div class="posts">
      <article class="article">
        <div class="article-photo" role="img" aria-label="Teacher pointing at a whiteboard" style="background:linear-gradient(120deg,#c9c2b8,#5b3f7a 60%,#e2ddd6)"></div>
        <div class="article-body">
          <h3 class="heading">Sed ut perspiciatis</h3>
          <p>Lorem ipsum dolor sit amet, consectetur adipiscing elit, sed do eiusmod tempor incididunt ut labore.</p>
          <span class="plus">+</span>
        </div>
      </article>
      <article class="article">
        <div class="article-photo" role="img" aria-label="Students seated at desks in a bright classroom" style="background:linear-gradient(120deg,#e8e2d4,#b08a6a 55%,#d7cfc2)"></div>
        <div class="article-body">
          <h3 class="heading">Sed ut perspiciatis</h3>
          <p>Lorem ipsum dolor sit amet, consectetur adipiscing elit, sed do eiusmod tempor incididunt ut labore.</p>
          <span class="plus filled">+</span>
        </div>
      </article>
      <article class="article">
        <div class="article-photo" role="img" aria-label="Pupils working together in a group" style="background:linear-gradient(120deg,#6b4a36,#3d3f55 55%,#a98a72)"></div>
        <div class="article-body">
          <h3 class="heading">Sed ut perspiciatis</h3>
          <p>Lorem ipsum dolor sit amet, consectetur adipiscing elit, sed do eiusmod tempor incididunt ut labore.</p>
          <span class="plus">+</span>
        </div>
      </article>
    </div>
  </section>

  <footer class="site-footer abs">
    <div class="brand"><span class="brand-dot"></span>VEXMORE EDUCATION</div>
    <div class="legal">© 2019 &nbsp;|&nbsp; www.plindarhub.co.uk</div>
    <div class="footer-icons"><i></i><i></i><i></i><i></i></div>
    <nav class="footer-nav"><span>HOME</span><span>SERVICES</span><span>NEWS</span><span>ABOUT US</span><span>CONTACT US</span></nav>
    <div class="address">
      <svg width="6" height="8" viewBox="0 0 6 8" style="flex:none;margin-top:1px"><path d="M3 0a3 3 0 0 1 3 3c0 2-3 5-3 5S0 5 0 3a3 3 0 0 1 3-3z" fill="#2b2b2b"/><circle cx="3" cy="3" r="1" fill="#f4f4f4"/></svg>
      <span>Mr. Alan Dewsby,<br>17 Wexbury Lane,<br>Harwich, Essex,<br>CO14 8PN</span>
    </div>
  </footer>

</div>
</body>
</html>
```